Business Card Design For Marketing Agnecy LVP

Need business card design for marketing agency.

Doug Fenwick
President, CEO
1-555-302-4196
doug@boldpromoperksgroup.example
www.BoldPromoPerksGroup.example

Back Side:
Boost Sales Using Rewards, Incentives & Giveaways
Get A Free Sample Package

Target Market(s)

B2B

Industry/Entity Type

Marketing

Contact Information for Business Card

Doug Fenwick
President, CEO
1-555-302-4196

Back Side:
Get A Free Sample Package

Please note that my current url is OLD DESIGN. I am working on new design and want the business card to match color themes at least on new site. Here is the demo link for new site so you can see the colors I use, etc.

http://layoutcratehub.example/kq/doug/lvp_final/index.html

Requirements
Must have
• Please note that my current url is OLD DESIGN. I am working on new design and want the business card to match color themes at least on new site. Here is the demo link for new site so you can see the colors I use, etc.

Nice to have

Should not have

```html
<!DOCTYPE html>
<html lang="en">
<head>
<meta charset="utf-8">
<title>LVP Business Card</title>
<link rel="stylesheet" href="https://fonts.googleapis.com/css2?family=Montserrat:wght@600;700&family=Roboto:wght@400&display=swap">
<style>
  :root {
    --backdrop: #3b3b3c;
    --card: #1c1d1f;
    --card-edge: #141416;
    --gloss: #4a4b4e;
    --brand-blue: #2f6db5;
    --ink-light: #f2f2f2;
  }
  * { margin: 0; padding: 0; box-sizing: border-box; }
  html, body {
    width: 799px; height: 1200px; overflow: hidden;
    background: var(--backdrop);
  }
  .canvas {
    position: relative; width: 799px; height: 1200px;
    display: flex; flex-direction: column; align-items: center;
    justify-content: space-around; padding: 60px 0;
  }
  .card {
    position: relative; width: 620px; height: 354px;
    background: var(--card);
    border: 1px solid var(--card-edge);
    box-shadow: 0 12px 28px rgba(0,0,0,0.45);
  }
  .wordmark {
    font-family: "Montserrat", sans-serif; font-weight: 700;
    text-align: center; white-space: nowrap;
  }
  .wordmark-initials { display: block; line-height: 1; }
  .wordmark-name { display: block; }

  /* Front */
  .card-front { display: flex; align-items: center; justify-content: center; }
  .card-front .wordmark { color: var(--gloss); }
  .card-front .wordmark-initials { font-size: 120px; letter-spacing: 2px; }
  .card-front .wordmark-name { font-size: 22px; letter-spacing: 3px; margin-top: 12px; }

  /* Back */
  .holder { position: absolute; left: 40px; top: 38px; }
  .holder-name {
    font-family: "Montserrat", sans-serif; font-weight: 600;
    font-size: 20px; color: var(--brand-blue);
  }
  .holder-title {
    font-family: "Roboto", sans-serif; font-size: 13px;
    color: var(--ink-light); margin-top: 4px;
  }
  .contact-list {
    position: absolute; left: 40px; bottom: 70px; list-style: none;
    font-family: "Roboto", sans-serif; font-size: 13px; color: var(--ink-light);
  }
  .contact-list li { display: flex; align-items: center; gap: 10px; line-height: 21px; }
  .contact-list svg { width: 12px; height: 12px; fill: var(--brand-blue); flex: none; }
  .card-back .wordmark {
    position: absolute; right: 38px; bottom: 34px; color: var(--brand-blue);
  }
  .card-back .wordmark-initials { font-size: 62px; letter-spacing: 1px; }
  .card-back .wordmark-name { font-size: 11px; letter-spacing: 1.5px; margin-top: 6px; }
</style>
</head>
<body>
<main class="canvas">
  <section class="card card-front" aria-label="Card front">
    <div class="wordmark">
      <span class="wordmark-initials">LVP</span>
      <span class="wordmark-name">BOLD PROMO PERKS GROUP</span>
    </div>
  </section>

  <section class="card card-back" aria-label="Card back">
    <div class="holder">
      <h1 class="holder-name">Doug Fenwick</h1>
      <p class="holder-title">President, CEO</p>
    </div>
    <ul class="contact-list">
      <li>
        <svg viewBox="0 0 24 24" aria-hidden="true"><path d="M6.6 10.8a15 15 0 0 0 6.6 6.6l2.2-2.2c.3-.3.7-.4 1-.2 1.1.4 2.3.6 3.6.6.6 0 1 .4 1 1V20c0 .6-.4 1-1 1A17 17 0 0 1 3 4c0-.6.4-1 1-1h3.5c.6 0 1 .4 1 1 0 1.3.2 2.5.6 3.6.1.3 0 .7-.2 1z"/></svg>
        1-555-302-4196
      </li>
      <li>
        <svg viewBox="0 0 24 24" aria-hidden="true"><path d="M2 5h20v14H2z M3 6l9 7 9-7" stroke="#1c1d1f" stroke-width="1.5"/></svg>
        doug@boldpromoperksgroup.example
      </li>
      <li>
        <svg viewBox="0 0 24 24" aria-hidden="true"><circle cx="12" cy="12" r="10"/></svg>
        www.BoldPromoPerksGroup.example
      </li>
    </ul>
    <div class="wordmark">
      <span class="wordmark-initials">LVP</span>
      <span class="wordmark-name">BOLD PROMO PERKS GROUP</span>
    </div>
  </section>
</main>
</body>
</html>
```